we can communicate on this, but i want to follow the approach we took on Pellew|Marsh & Quinlan but i feel the card front needs the black background and the platinum and gold logo. The back? I am open. we can use the same info from PM&Q. Velmont Arc is an enhanced equity investment fund - basically a very exclusive boutique hedge fund that uses only stock options. very advanced things. hope you are interested

Contact Information for Business Card

Dr. Lewis T. Brennick, CFA
Scientifique de fusée financière
701.555.0143
LTBquant47@mailvantor.com

4718 Willow Creek Bend W.
West Fargo, ND 58078

No web site

Colors

Designer to choose colors to be used in the design.

Requirements
Nice to have
• I tend to prefer the most visible applications of the logo to include logo and name, the logo version with a black background and the gold and platinum components separated by the black. I see this working well for a single side (logo and name - this is card front to me).
• I am fairly open to other treatments on the reverse side with the data. To me, it makes sense to have a different color rendition of the logo on the reverse and it may be a muted black tone on tone or an oversized portion that would have spot UV. Or, the reverse may play with colors and layout
Should not have
• Other colors = no no
• Decorative font

```html
<!DOCTYPE html>
<html lang="en">
<head>
<meta charset="utf-8">
<title>Velmont Arc — Business Card</title>
<link href="https://fonts.googleapis.com/css2?family=Montserrat:wght@600&family=Lato:wght@400;700&display=swap" rel="stylesheet">
<style>
  :root {
    --backdrop: #5a5f61;
    --card-black: #111112;
    --gold: #c9a03a;
    --gold-light: #e2c06a;
    --white: #ffffff;
    --muted: #8a8a8c;
  }
  * { margin: 0; padding: 0; box-sizing: border-box; }
  html, body { width: 1200px; height: 780px; overflow: hidden; }
  body {
    background: var(--backdrop);
    position: relative;
    font-family: "Lato", Arial, sans-serif;
  }
  .card {
    position: absolute;
    top: 230px;
    width: 560px;
    height: 320px;
    background: var(--card-black);
    box-shadow: 0 8px 24px rgba(0,0,0,0.35);
  }
  .card-front { left: 20px; }
  .card-back { left: 620px; }

  .brand {
    position: absolute;
    display: flex;
    flex-direction: column;
    align-items: center;
    gap: 14px;
  }
  .brand-mark {
    display: block;
    border-radius: 50%;
    background: linear-gradient(135deg, var(--gold) 0%, var(--gold-light) 50%, var(--gold) 100%);
  }
  .brand-name {
    font-family: "Montserrat", Arial, sans-serif;
    font-weight: 600;
    color: var(--white);
    text-transform: uppercase;
    letter-spacing: 0.04em;
    white-space: nowrap;
  }

  .card-front .brand { left: 0; right: 0; top: 70px; }
  .card-front .brand-mark { width: 110px; height: 110px; }
  .card-front .brand-name { font-size: 40px; }

  .card-back .brand { right: 34px; top: 28px; gap: 10px; }
  .card-back .brand-mark { width: 86px; height: 86px; }
  .card-back .brand-name { font-size: 30px; }

  .person {
    position: absolute;
    left: 36px;
    top: 178px;
  }
  .person-name {
    font-weight: 700;
    font-size: 19px;
    color: var(--gold);
  }
  .person-title {
    font-size: 12px;
    color: var(--muted);
    margin-top: 2px;
  }
  .divider {
    position: absolute;
    left: 36px;
    right: 36px;
    top: 232px;
    height: 1px;
    background: var(--gold);
  }
  .contact-list {
    position: absolute;
    left: 36px;
    top: 248px;
    list-style: none;
  }
  .contact-item {
    display: flex;
    align-items: center;
    gap: 12px;
    font-size: 13px;
    color: var(--muted);
    height: 24px;
    white-space: nowrap;
  }
  .contact-icon { width: 14px; height: 14px; flex: none; }
  .contact-icon-phone { fill: var(--gold); }
  .contact-icon-mail { fill: none; stroke: var(--gold); stroke-width: 2; }
  .address {
    position: absolute;
    right: 36px;
    top: 246px;
    text-align: right;
    font-style: normal;
    font-size: 13px;
    line-height: 20px;
    color: var(--muted);
    white-space: nowrap;
  }
</style>
</head>
<body>

  <section class="card card-front" aria-label="Card front">
    <div class="brand">
      <span class="brand-mark"></span>
      <span class="brand-name">Velmont Arc</span>
    </div>
  </section>

  <section class="card card-back" aria-label="Card back">
    <div class="brand">
      <span class="brand-mark"></span>
      <span class="brand-name">Velmont Arc</span>
    </div>

    <div class="person">
      <p class="person-name">Dr. Lewis T. Brennick, CFA</p>
      <p class="person-title">Scientifique des Fusées Financières</p>
    </div>

    <div class="divider"></div>

    <ul class="contact-list">
      <li class="contact-item">
        <svg class="contact-icon contact-icon-phone" viewBox="0 0 24 24" aria-hidden="true"><path d="M6.6 10.8a15.1 15.1 0 0 0 6.6 6.6l2.2-2.2a1 1 0 0 1 1-.25 11.4 11.4 0 0 0 3.6.57 1 1 0 0 1 1 1V20a1 1 0 0 1-1 1A17 17 0 0 1 3 4a1 1 0 0 1 1-1h3.5a1 1 0 0 1 1 1c0 1.25.2 2.46.57 3.6a1 1 0 0 1-.25 1z"/></svg>
        <span>701.555.0143</span>
      </li>
      <li class="contact-item">
        <svg class="contact-icon contact-icon-mail" viewBox="0 0 24 24" aria-hidden="true"><path d="M2 5h20v14H2z M2 5l10 8 10-8"/></svg>
        <span>LTBquant47@mailvantor.com</span>
      </li>
    </ul>

    <address class="address">
      4718 Willow Creek Bend W.<br>
      West Fargo, ND 58078
    </address>
  </section>

</body>
</html>
```